Medical Practice needs a Letterhead Design

We need a clean, modern letterhead design for our stem cell medical practice.

Industry/Entity Type

Medical

```html
<!DOCTYPE html>
<html lang="en">
<head>
<meta charset="utf-8">
<title>Brightmoor Clinic Letterhead</title>
<link rel="stylesheet" href="https://fonts.googleapis.com/css2?family=Arimo:wght@400;700&display=swap">
<style>
  :root {
    --navy: #0b3349;
    --lime: #b5c637;
    --paper: #ffffff;
    --backdrop: #e9ecef;
    --ink: #1d2a33;
    --motif-grey: #c4c4cc;
    --motif-green: #e8ebd3;
  }
  * { box-sizing: border-box; margin: 0; padding: 0; }
  html, body {
    width: 1200px;
    height: 800px;
    overflow: hidden;
    background: var(--backdrop);
    font-family: "Arimo", Arial, sans-serif;
  }
  .canvas {
    position: relative;
    width: 1200px;
    height: 800px;
  }
  .letterhead {
    position: absolute;
    left: 330px;
    top: 30px;
    width: 539px;
    height: 740px;
    background: var(--paper);
    box-shadow: 0 6px 18px rgba(0, 0, 0, 0.18);
    overflow: hidden;
  }
  .top-band {
    position: absolute;
    top: 0;
    left: 0;
    width: 100%;
    height: 15px;
    display: flex;
  }
  .top-band__navy { width: 351px; background: var(--navy); }
  .top-band__lime { flex: 1; background: var(--lime); }
  .brand-motif {
    position: absolute;
    left: 0;
    bottom: 0;
    width: 336px;
    height: 333px;
    background: radial-gradient(ellipse at 20% 70%, var(--motif-green) 0%, rgba(232, 235, 211, 0.55) 40%, rgba(255, 255, 255, 0) 72%),
                radial-gradient(ellipse at 35% 20%, rgba(196, 196, 204, 0.35) 0%, rgba(255, 255, 255, 0) 55%);
  }
  .footer {
    position: absolute;
    right: 17px;
    bottom: 31px;
    text-align: right;
    color: var(--ink);
  }
  .brand-name {
    display: flex;
    align-items: center;
    justify-content: flex-end;
    gap: 7px;
    margin-bottom: 12px;
    font-size: 22px;
    line-height: 24px;
    font-weight: 400;
    color: var(--navy);
  }
  .brand-name__dot {
    width: 11px;
    height: 11px;
    border-radius: 50%;
    background: var(--lime);
  }
  .contact-line {
    font-size: 9.5px;
    line-height: 10px;
    white-space: nowrap;
  }
</style>
</head>
<body>
  <main class="canvas">
    <article class="letterhead">
      <div class="top-band">
        <div class="top-band__navy"></div>
        <div class="top-band__lime"></div>
      </div>

      <div class="brand-motif" role="img" aria-label="Soft decorative brand motif area in pale grey and green"></div>

      <footer class="footer">
        <div class="brand-name">
          <span class="brand-name__dot"></span>
          <span>Brightmoor Clinic</span>
        </div>
        <p class="contact-line">Address line 1</p>
        <p class="contact-line">Tel:00 00 0000 0000 Fax : 00000000 Mobile :00 00000 00000</p>
        <p class="contact-line">Email: hello@brightmoorclinic.com Website:www.brightmoorclinic.com</p>
      </footer>
    </article>
  </main>
</body>
</html>
```